Copper Lantern

Need a business card for our restaurant. Restaurant and Bar in the mountains of North Idaho. Rustic looking card

rustic design, wood and metal looking, primarily neutral colors

• Name, address, phone number, website, email address

```html
<!DOCTYPE html>
<html lang="en">
<head>
<meta charset="utf-8">
<title>Copper Lantern – Business Card</title>
<link rel="stylesheet" href="https://fonts.googleapis.com/css2?family=Roboto:wght@400;700&display=swap">
<style>
  :root {
    --bg: #2b2b2c;
    --card: #ffffff;
    --ink: #0c0c0c;
    --muted: #1c1c1c;
    --radius: 26px;
  }
  * { margin: 0; padding: 0; box-sizing: border-box; }
  html, body { width: 1200px; height: 993px; overflow: hidden; }
  body {
    background: var(--bg);
    font-family: "Roboto", Arial, sans-serif;
    color: var(--ink);
    position: relative;
  }
  .card {
    position: absolute;
    top: 196px;
    width: 360px;
    height: 600px;
    background: var(--card);
    border-radius: var(--radius);
  }
  .card--front { left: 150px; }
  .card--back { left: 690px; }

  .brand {
    position: absolute;
    left: 50%;
    transform: translateX(-50%);
    width: 210px;
    height: 210px;
    border: 6px solid var(--ink);
    border-radius: 50%;
    display: flex;
    align-items: center;
    justify-content: center;
    text-align: center;
  }
  .brand__name {
    font-weight: 700;
    font-size: 26px;
    line-height: 1.15;
    letter-spacing: 2px;
    text-transform: uppercase;
    color: var(--ink);
  }
  .card--front .brand { top: 195px; }
  .card--back .brand { top: 40px; }

  .contact {
    position: absolute;
    top: 290px;
    left: 42px;
    right: 30px;
  }
  .dots { display: block; width: 280px; height: 14px; }
  .contact__name {
    font-weight: 700;
    font-size: 25px;
    margin-top: 14px;
  }
  .contact__role {
    font-size: 15px;
    margin-top: 2px;
    margin-bottom: 14px;
  }
  .contact__icons {
    display: flex;
    gap: 6px;
    margin: 14px 0 10px;
  }
  .icon {
    width: 24px;
    height: 24px;
    border-radius: 50%;
    background: var(--ink);
    display: flex;
    align-items: center;
    justify-content: center;
  }
  .icon svg { width: 14px; height: 14px; }
  .contact__line {
    font-size: 16px;
    line-height: 1.35;
    color: var(--muted);
  }
  .contact__address { margin-top: 12px; margin-bottom: 14px; }
</style>
</head>
<body>
  <section class="card card--front">
    <div class="brand"><span class="brand__name">Copper<br>Lantern</span></div>
  </section>

  <section class="card card--back">
    <div class="brand"><span class="brand__name">Copper<br>Lantern</span></div>

    <div class="contact">
      <svg class="dots" viewBox="0 0 280 14" aria-hidden="true">
        <g fill="#0c0c0c">
          <circle cx="5" cy="7" r="2.5"/><circle cx="17" cy="7" r="3"/><circle cx="30" cy="7" r="3.5"/>
          <circle cx="45" cy="7" r="4"/><circle cx="61" cy="7" r="4.5"/><circle cx="78" cy="7" r="5"/>
          <circle cx="96" cy="7" r="5.5"/><circle cx="115" cy="7" r="6"/><circle cx="134" cy="7" r="6"/>
          <circle cx="153" cy="7" r="5.5"/><circle cx="171" cy="7" r="5"/><circle cx="188" cy="7" r="4.5"/>
          <circle cx="204" cy="7" r="4"/><circle cx="219" cy="7" r="3.5"/><circle cx="233" cy="7" r="3"/>
          <circle cx="246" cy="7" r="2.5"/><circle cx="258" cy="7" r="2"/><circle cx="269" cy="7" r="2"/>
        </g>
      </svg>
      <h1 class="contact__name">Owen Hartley</h1>
      <p class="contact__role">Managing Director</p>

      <div class="contact__icons">
        <span class="icon"><svg viewBox="0 0 24 24"><path fill="#fff" d="M6.6 10.8a15 15 0 0 0 6.6 6.6l2.2-2.2c.3-.3.7-.4 1-.2 1.1.4 2.3.6 3.6.6.6 0 1 .4 1 1V20c0 .6-.4 1-1 1A17 17 0 0 1 3 4c0-.6.4-1 1-1h3.5c.6 0 1 .4 1 1 0 1.3.2 2.5.6 3.6.1.3 0 .7-.2 1z"/></svg></span>
        <span class="icon"><svg viewBox="0 0 24 24"><path fill="#fff" d="M3 5h18v14H3z"/><path fill="none" stroke="#0c0c0c" stroke-width="2" d="M3 6l9 7 9-7"/></svg></span>
        <span class="icon"><svg viewBox="0 0 24 24"><g fill="none" stroke="#fff" stroke-width="2"><circle cx="12" cy="12" r="9"/><path d="M3 12h18M12 3c3 3 3 15 0 18M12 3c-3 3-3 15 0 18"/></g></svg></span>
      </div>
      <p class="contact__line">123 456 789</p>
      <p class="contact__line">info@yourmail.com</p>
      <p class="contact__line">www.yourwebsite.com</p>

      <div class="contact__icons">
        <span class="icon"><svg viewBox="0 0 24 24"><path fill="#fff" d="M12 2a7 7 0 0 0-7 7c0 5 7 13 7 13s7-8 7-13a7 7 0 0 0-7-7zm0 9.5A2.5 2.5 0 1 1 12 6.5a2.5 2.5 0 0 1 0 5z"/></svg></span>
      </div>
      <p class="contact__line">Your address, City</p>
      <p class="contact__line contact__address" style="margin-top:0">State, Zip 1234</p>

      <svg class="dots" viewBox="0 0 280 14" aria-hidden="true">
        <g fill="#0c0c0c">
          <circle cx="5" cy="7" r="2.5"/><circle cx="17" cy="7" r="3"/><circle cx="30" cy="7" r="3.5"/>
          <circle cx="45" cy="7" r="4"/><circle cx="61" cy="7" r="4.5"/><circle cx="78" cy="7" r="5"/>
          <circle cx="96" cy="7" r="5.5"/><circle cx="115" cy="7" r="6"/><circle cx="134" cy="7" r="6"/>
          <circle cx="153" cy="7" r="5.5"/><circle cx="171" cy="7" r="5"/><circle cx="188" cy="7" r="4.5"/>
          <circle cx="204" cy="7" r="4"/><circle cx="219" cy="7" r="3.5"/><circle cx="233" cy="7" r="3"/>
          <circle cx="246" cy="7" r="2.5"/><circle cx="258" cy="7" r="2"/><circle cx="269" cy="7" r="2"/>
        </g>
      </svg>
    </div>
  </section>
</body>
</html>
```